Business Card Design Project

Business Card design based on logo.
Updates

I need business card, letterhead, envelope, and if possible, Powerpoint slide template.

On front of business card: Just logo- and  my name and title:  Harriet Lindqvist, Principal

On reverse-logo and the rest of the contact info:

4871 Quarry Lane
Davis, CA 95618
650-318-2764
hl@brackenstudyworks.example

On letterhead-Just logo at top, at bottom  the rest-very small along the bottom

On PPT slide-just the logo.

I also want to try a few other colors-I like lime/dark grey (not black) but would like to try Sienna, maybe also indigo or bright blue-green.

I forgot to add-

On the business card-switch to vertical on reverse side and put:

Reverse side-switch to vertical and list:

Harriet Lindqvist
Principal
Bracken Study Works, LLC

650-318-2764

4871 Quarry Lane
Davis, CA 95618

Harriet Lindqvist
Principal

650-318-2764

4871 Quarry Lane
Davis, CA 95618

I have another project at the same time-for Stationery. Feel free to submit to that one also.

That one includes letterhead, envelope, PPT slide, folder cover sheet-HL

Industry/Entity Type

Business

Requirements
Must have
• Must use logo-preferably lime green version-with gray, not black or just 2-tone -logo on colored background.

```html
<!DOCTYPE html>
<html lang="en">
<head>
<meta charset="utf-8">
<title>Bracken Study Works – Business Card</title>
<link rel="stylesheet" href="https://fonts.googleapis.com/css2?family=Source+Sans+3:wght@400;600;700&display=swap">
<style>
  :root {
    --backdrop: #1f1f1f;
    --card-white: #ffffff;
    --lime: #8cb82b;
    --slate: #4a4a4c;
    --ink: #4b4b4b;
    --panel-text: #f2f2f2;
  }
  * { box-sizing: border-box; margin: 0; padding: 0; }
  html, body { width: 1200px; height: 722px; overflow: hidden; }
  body {
    background: var(--backdrop);
    font-family: "Source Sans 3", Arial, sans-serif;
    position: relative;
  }
  .card {
    position: absolute;
    width: 525px;
    height: 300px;
    border-radius: 14px;
    background: var(--card-white);
    overflow: hidden;
  }
  .card--front { left: 58px; top: 215px; }
  .card--back  { left: 617px; top: 208px; }

  .brand {
    position: absolute;
    display: flex;
    flex-direction: column;
    align-items: center;
  }
  .brand__mark {
    width: 22px; height: 22px;
    background: var(--lime);
    margin-bottom: 14px;
  }
  .brand__name {
    color: var(--ink);
    font-weight: 600;
    font-size: 34px;
    line-height: 1.05;
    letter-spacing: 3px;
    text-transform: uppercase;
    text-align: center;
  }
  .card--front .brand { left: 0; right: 0; top: 92px; }
  .holder {
    position: absolute;
    left: 0; right: 0; top: 241px;
    text-align: center;
    font-size: 17px;
    color: var(--ink);
  }
  .holder__name { color: var(--lime); font-weight: 700; text-transform: uppercase; }
  .holder__title { font-size: 14px; }

  .card--back .brand { left: 0; width: 285px; top: 80px; }
  .card--back .brand__name { font-size: 30px; }
  .divider {
    position: absolute; left: 285px; top: 0; bottom: 0;
    width: 4px; background: var(--lime);
  }
  .contact-panel {
    position: absolute; left: 289px; top: 0; right: 0; bottom: 0;
    background: var(--slate);
    color: var(--panel-text);
    padding: 74px 0 0 10px;
  }
  .contact-panel__company {
    color: var(--lime); font-weight: 700; font-size: 17px; line-height: 20px;
  }
  .contact-panel__address { margin-top: 14px; font-size: 14px; line-height: 19px; }
  .contact-list { list-style: none; margin-top: 14px; font-size: 13.5px; }
  .contact-list li { display: flex; align-items: center; gap: 7px; height: 21px; }
  .contact-list svg { width: 11px; height: 11px; fill: var(--lime); flex: none; }
</style>
</head>
<body>
  <section class="card card--front" aria-label="Card front">
    <div class="brand">
      <span class="brand__mark"></span>
      <span class="brand__name">Bracken<br>Study Works</span>
    </div>
    <p class="holder"><span class="holder__name">Harriet Lindqvist,</span> <span class="holder__title">Principal</span></p>
  </section>

  <section class="card card--back" aria-label="Card back">
    <div class="brand">
      <span class="brand__mark"></span>
      <span class="brand__name">Bracken<br>Study Works</span>
    </div>
    <div class="divider"></div>
    <div class="contact-panel">
      <p class="contact-panel__company">Bracken<br>Study Works, LLC</p>
      <p class="contact-panel__address">4871 Quarry Lane<br>Davis, CA 95618</p>
      <ul class="contact-list">
        <li><svg viewBox="0 0 12 12" aria-hidden="true"><path d="M2.5 0.5l2 2.5-1.2 1.3c.7 1.6 2 2.9 3.5 3.6l1.3-1.2 2.4 2-1.3 2.3C4.6 10.7 1.3 7.4.5 2z"/></svg>650-318-2764</li>
        <li><svg viewBox="0 0 12 12" aria-hidden="true"><path d="M0 2.5h12v7H0z M0.8 3.2L6 7l5.2-3.8" stroke="#4a4a4c" stroke-width="0.8"/></svg>hl@brackenstudyworks.example</li>
        <li><svg viewBox="0 0 12 12" aria-hidden="true"><circle cx="6" cy="6" r="5.5"/><path d="M0.5 6h11M6 0.5v11M6 0.5c-2.5 3-2.5 8 0 11M6 0.5c2.5 3 2.5 8 0 11" stroke="#4a4a4c" stroke-width="0.7" fill="none"/></svg>www.brackenstudyworks.example</li>
      </ul>
    </div>
  </section>
</body>
</html>
```